Flat Belly Design Graphics for Social

I want to create 9 social media graphics (new Instagram size 4:5 (1080 x 1350 pixels) focusing on our Flat Belly Graphics, using the pics attached. Use the attached pics, NO RANDOM STOCK PHOTOGRAPHY. For the color scheme of the graphics, the color palette is attached. YOU MUST POST ALL 9 GRAPHICS IN ONE ENTRY.
Using the 3 titles below, create one set of graphics. 1) with all text, then for the others, use the pictures as detailed below in IMPORTANT:
1. Ten-Week Bright Morning Reboot
2. The Quick Garden Kitchen Menu Guide
3. Studio Habits for Lasting Energy Past Midlife - Zero Gym Needed
IMPORTANT:
Only use RK Pic 1 and RK Pic 2 with the title, Ten-Week Bright Morning Reboot
Only use meal plan1 and meal plan2 pics with the title, Quick Garden Kitchen Menu Guide
Only use studio habits 1 and studio habits 2 pics with the title, Studio Habits for Lasting Energy Past Midlife - Zero Gym Needed
women over 40

```html
<!DOCTYPE html>
<html lang="en">
<head>
<meta charset="utf-8">
<title>Bright Morning Social Set</title>
<link rel="stylesheet" href="https://fonts.googleapis.com/css2?family=Oswald:wght@500;600;700&display=swap">
<style>
:root{
  --stage:#2c1019;
  --blush:#fbeeef;
  --rose:#dc7d9a;
  --rose-mid:#e497b0;
  --rose-pale:#f8d7e3;
  --forest:#2f4a48;
  --teal:#5aa89a;
  --white:#ffffff;
}
*{margin:0;padding:0;box-sizing:border-box}
html,body{width:1074px;height:1200px;overflow:hidden;background:var(--stage)}
body{position:relative;font-family:"Oswald",sans-serif;font-weight:600;line-height:1}
.post{position:absolute;width:259px;height:324px;background:var(--blush);overflow:hidden}
.c1{left:122px}.c2{left:408px}.c3{left:693px}
.r1{top:94px}.r2{top:438px}.r3{top:782px}
.line{display:block;white-space:nowrap;text-transform:uppercase}
.photo{position:absolute;display:block}
.band{position:absolute;left:0;right:0;bottom:0;display:flex;align-items:center;justify-content:center}
.panel{position:absolute;left:11px;right:11px;display:flex;flex-direction:column;align-items:center;justify-content:center;text-align:center}
.strip{display:block;padding:3px 0;width:196px;text-align:center;letter-spacing:4px;font-size:17px}

.reboot-type .stack{position:absolute;left:21px;top:30px}
.reboot-type .band{height:81px;background:var(--rose)}
.reboot-type .tag{font-size:40px;color:var(--white);background:var(--forest);padding:2px 14px}
.menu-type .stack{position:absolute;left:0;right:0;top:18px;text-align:center}
.menu-type .band{height:72px;background:var(--forest)}
.habits-type .stack{position:absolute;left:22px;top:22px}
.habits-type .band{height:54px;background:var(--rose)}
</style>
</head>
<body>

<section class="post c1 r1 reboot-type">
  <div class="stack">
    <span class="line" style="font-size:34px;color:var(--rose)">Ten-Week</span>
    <span class="line" style="font-size:62px;color:var(--forest);margin-top:4px">Bright</span>
    <span class="line" style="font-size:52px;color:var(--forest);margin-top:4px">Morning</span>
  </div>
  <div class="band"><span class="tag">Reboot</span></div>
</section>

<section class="post c2 r1 menu-type">
  <div class="stack">
    <span class="line" style="font-size:30px;color:var(--forest);text-transform:none">The Quick</span>
    <span class="line" style="font-size:70px;color:var(--rose);text-transform:none;margin-top:6px">Garden</span>
    <span class="line" style="font-size:54px;color:var(--rose);margin-top:6px">Kitchen</span>
  </div>
  <div class="band"><span style="font-size:40px;color:var(--white)">Menu Guide</span></div>
</section>

<section class="post c3 r1 habits-type">
  <div class="stack">
    <span class="line" style="font-size:19px;color:var(--rose);text-transform:none">Studio Habits for</span>
    <span class="line" style="font-size:60px;color:var(--forest);margin-top:8px">Lasting</span>
    <span class="line" style="font-size:60px;color:var(--rose);margin-top:6px">Energy</span>
    <span class="line" style="font-size:38px;color:var(--forest);margin-top:8px">Past Midlife</span>
  </div>
  <div class="band"><span style="font-size:25px;color:var(--white)">Zero Gym Needed</span></div>
</section>

<section class="post c1 r2">
  <div class="photo" role="img" aria-label="Smiling woman in a white cropped sweater pointing to her toned midriff" style="left:55px;top:20px;width:150px;height:185px;background:linear-gradient(180deg,#3a2a26 0%,#efe6e4 35%,#c89a80 70%,#1c1c1c 100%)"></div>
  <div class="panel" style="top:205px;height:106px;background:var(--rose-pale)">
    <span class="line" style="font-size:19px;color:var(--teal);text-transform:none">Ten-Week</span>
    <span class="line" style="font-size:29px;color:var(--forest);margin-top:3px">Bright Morning</span>
    <span class="strip" style="background:var(--rose);color:var(--blush);margin-top:4px">Reboot</span>
  </div>
</section>

<section class="post c2 r2">
  <div class="photo" role="img" aria-label="Healthy foods around a paper meal planner on a wooden table" style="left:0;top:0;width:259px;height:178px;background:radial-gradient(circle at 50% 55%,#f2f0ec 0 18%,transparent 30%),linear-gradient(135deg,#e9b8a8,#5a3a2a 45%,#c8432f 75%,#6b8a3a)"></div>
  <div class="panel" style="top:190px;height:120px;background:var(--rose-mid)">
    <span class="line" style="font-size:19px;color:var(--forest);text-transform:none">The Quick</span>
    <span class="line" style="font-size:29px;color:var(--forest);margin-top:3px">Garden Kitchen</span>
    <span class="strip" style="background:var(--rose-pale);color:var(--forest);margin-top:4px">Menu Guide</span>
  </div>
</section>

<section class="post c3 r2">
  <div class="photo" role="img" aria-label="Two women sharing a secret, one looking delighted" style="left:0;top:0;width:259px;height:176px;background:linear-gradient(135deg,#3a2418 0%,#b07a5a 40%,#e8e8ea 70%,#caa88a 100%)"></div>
  <div class="panel" style="top:190px;height:120px;background:var(--rose-pale)">
    <span class="line" style="font-size:19px;color:var(--teal);text-transform:none">Studio Habits for</span>
    <span class="line" style="font-size:30px;color:var(--forest);margin-top:3px">Lasting Energy</span>
    <span class="strip" style="background:var(--rose);color:var(--white);letter-spacing:0;font-size:13px;width:206px;margin-top:4px">Past Midlife - Zero Gym Needed</span>
  </div>
</section>

<section class="post c1 r3">
  <div class="photo" role="img" aria-label="Smiling woman in a white cropped sweater in a kitchen, pointing to her midriff" style="left:0;top:0;width:130px;height:324px;background:linear-gradient(180deg,#5a3a2a 0%,#8a6a58 30%,#ece4e2 50%,#b88a70 68%,#1c1c1c 100%)"></div>
  <div style="position:absolute;left:130px;top:0;width:129px;height:324px;background:var(--forest);padding:20px 0 0 12px">
    <span class="line" style="font-size:20px;color:var(--rose);text-transform:none">Ten-Week</span>
    <span class="line" style="font-size:34px;color:var(--white);margin-top:8px">Bright</span>
    <span class="line" style="font-size:28px;color:var(--rose);text-transform:none;margin-top:4px">Morning</span>
    <span class="line" style="font-size:34px;color:var(--white);margin-top:130px">Reboot</span>
  </div>
</section>

<section class="post c2 r3" style="background:var(--forest)">
  <div style="position:absolute;left:0;right:0;top:16px;text-align:center">
    <span class="line" style="font-size:34px;color:var(--rose);text-transform:none">The Quick</span>
    <span class="line" style="font-size:31px;color:var(--white);margin-top:6px">Garden Kitchen</span>
    <span class="strip" style="margin:7px auto 0;width:216px;background:var(--rose);color:var(--forest)">Menu Guide</span>
  </div>
  <div class="photo" role="img" aria-label="Colourful vegetables, fruit, fish and meat framing a small meal plan notebook" style="left:0;top:162px;width:259px;height:162px;background:radial-gradient(ellipse at 50% 50%,#3a2a22 0 30%,transparent 45%),linear-gradient(135deg,#d04030,#e0a030 30%,#6a9a3a 55%,#e07050 80%,#8a2a2a)"></div>
</section>

<section class="post c3 r3" style="background:var(--forest)">
  <div class="photo" role="img" aria-label="Two women on a bright blue background, one whispering to the other" style="left:0;top:0;width:259px;height:175px;background:linear-gradient(135deg,#6cc4dc,#4ab0cc 50%,#5abcd4)"></div>
  <div style="position:absolute;left:0;right:0;top:194px;text-align:center">
    <span class="line" style="font-size:24px;color:var(--white);text-transform:none">Studio Habits for</span>
    <span class="line" style="font-size:34px;color:var(--white);margin-top:6px">Lasting Energy</span>
  </div>
  <div class="band" style="height:38px;background:var(--rose)"><span style="font-size:17px;color:var(--white);font-weight:500">Past Midlife - Zero Gym Needed</span></div>
</section>

</body>
</html>
```